Marlowby Services Website Design

We have most content but require a professional design. We have a logo already and will need it utilized along with several of the photos from the attached documentation.
First page should have our mission and Vision and the synapsis provided in the word document. Visitors will be prompted to select from one of our 3 divisions from this page.
Each division will have the same list of tabs : About, Services, Safety, Careers and Contact.
Photos on each divisions page should be representative of the divisions offerings. The word doc attached contains the requested content and we are open to edits that would complement and fill the website.
I like the Quorvane site www.quorvane.example - they are our competition so cant be modeled directly after this.
Please include prompts to request quote at each service page. align the format of the geotechnical page to the other 2 divisions.
I used chat gpt for some of the content so will need it optimized for SCO.

```html
<!DOCTYPE html>
<html lang="en">
<head>
<meta charset="utf-8">
<title>Marlowby Services</title>
<link href="https://fonts.googleapis.com/css2?family=Krona+One&family=Poppins:wght@400;500&family=Open+Sans:wght@700&display=swap" rel="stylesheet">
<style>
:root{
  --red:#e41e26;
  --ink:#231f20;
  --text:#333333;
  --white:#ffffff;
  --light:#f2f2f2;
  --mist:#e9eaec;
  --footer:#2b2b2b;
  --head:'Krona One',sans-serif;
  --body:'Poppins',sans-serif;
  --btn:'Open Sans',sans-serif;
}
*{margin:0;padding:0;box-sizing:border-box}
html,body{width:1200px;height:2414px;overflow:hidden}
body{font-family:var(--body);color:var(--text);background:var(--white);position:relative}
.hero{position:absolute;left:0;top:0;width:1200px;height:654px;
  background:linear-gradient(135deg,#8a7760 0%,#6d5c48 35%,#4e4236 60%,#8a8379 100%)}
.hero-shade{position:absolute;inset:0;background:linear-gradient(90deg,rgba(40,30,20,.35),rgba(0,0,0,0))}
.brand{position:absolute;left:75px;top:48px;display:flex;align-items:center;gap:12px;
  font-family:var(--head);font-size:34px;color:var(--white);letter-spacing:2px}
.brand-mark{width:26px;height:26px;background:var(--white)}
.menu{position:absolute;left:1098px;top:54px;width:28px}
.hero h1{position:absolute;left:75px;top:262px;font-family:var(--head);font-weight:400;
  font-size:37px;line-height:46px;color:var(--white);letter-spacing:1.5px}
.btn{display:inline-flex;align-items:center;justify-content:center;background:var(--red);
  color:var(--white);font-family:var(--btn);font-weight:700;font-size:14px;text-decoration:none}
.hero .btn{position:absolute;left:75px;top:378px;width:151px;height:48px}
.section-title{font-family:var(--head);font-weight:400;font-size:34px;color:var(--ink);letter-spacing:1.5px}
.section-title span{color:var(--red)}
.vision{position:absolute;left:0;top:654px;width:1200px;height:241px;text-align:center}
.vision .section-title{margin-top:56px}
.vision p{font-size:18.5px;line-height:33.5px;margin:22px auto 0;width:1040px}
.mission{position:absolute;left:0;top:895px;width:1200px;height:486px;
  background:linear-gradient(180deg,#dfe2e4 0%,#eceeef 45%,#e4e5e6 100%)}
.mission-photo{position:absolute;inset:0;background:linear-gradient(90deg,rgba(255,255,255,.25),rgba(210,212,214,.35) 50%,rgba(255,255,255,.2))}
.mission-title{position:absolute;left:70px;top:45px;height:400px;display:flex;
  flex-direction:row;align-items:flex-end;gap:4px}
.mission-title div{writing-mode:vertical-rl;transform:rotate(180deg);
  font-family:var(--head);font-size:40px;line-height:44px;letter-spacing:2px}
.mission-title .m1{color:var(--red)}
.mission-title .m2{color:var(--ink)}
.mission p{position:absolute;left:226px;top:140px;width:910px;font-size:18.5px;line-height:33.6px}
.divisions{position:absolute;left:0;top:1381px;width:1200px;height:524px}
.divisions .section-title{text-align:center;margin-top:56px}
.cards{position:absolute;left:75px;top:127px;display:flex;gap:31px}
.card{position:relative;width:330px;height:316px}
.card-shade{position:absolute;inset:0;background:linear-gradient(180deg,rgba(0,0,0,0) 45%,rgba(0,0,0,.85) 100%)}
.card h3{position:absolute;left:0;right:0;bottom:24px;text-align:center;font-family:var(--head);
  font-weight:400;font-size:23px;line-height:27px;color:var(--white);letter-spacing:1.5px}
.aerial{background:linear-gradient(160deg,#6f7070,#8c8c88 40%,#5d6a4f 100%)}
.drilling{background:linear-gradient(180deg,#6f8a4c,#8ea26a 45%,#5b4e40 100%)}
.renewable{background:linear-gradient(160deg,#c99a5a,#7f6e58 45%,#3b4a66 100%)}
.services{position:absolute;left:0;top:1905px;width:1200px;height:430px;background:var(--light)}
.services-photo{position:absolute;left:75px;top:53px;width:513px;height:325px;
  background:linear-gradient(180deg,#4d5c44 0%,#7d8574 45%,#b9b6ad 100%)}
.services-copy{position:absolute;left:616px;top:103px;width:520px}
.services-copy p{font-size:18.5px;line-height:33.6px;margin-top:20px}
.services-copy .btn{width:152px;height:48px;margin-top:28px}
.footer{position:absolute;left:0;top:2335px;width:1200px;height:79px;background:var(--footer);color:var(--white)}
.footer small{position:absolute;left:75px;top:32px;font-size:12.5px}
.social{position:absolute;right:75px;top:28px;display:flex;gap:20px}
.social span{width:20px;height:20px;border-radius:50%;background:var(--white)}
</style>
</head>
<body>
<header class="hero">
  <div class="hero-shade" role="img" aria-label="Photo of a white aerial boom truck parked on a dirt lot"></div>
  <div class="brand"><span class="brand-mark"></span>MARLOWBY</div>
  <svg class="menu" viewBox="0 0 28 24" aria-label="Menu"><rect y="0" width="28" height="4" fill="#fff"/><rect y="10" width="28" height="4" fill="#fff"/><rect y="20" width="28" height="4" fill="#fff"/></svg>
  <h1>WELCOME TO<br>MARLOWBY SERVICES</h1>
  <a class="btn" href="#">REQUEST QUOTE</a>
</header>

<section class="vision">
  <h2 class="section-title">OUR <span>VISION</span></h2>
  <p>To be the leading provider of aerial access, geotechnical drilling, and service solutions, setting the standard for excellence in safety, efficiency, and environmental stewardship.</p>
</section>

<section class="mission">
  <div class="mission-photo" role="img" aria-label="Faded photo of a boom truck in front of a facility"></div>
  <div class="mission-title"><div class="m1">MISSION</div><div class="m2">STATEMENT</div></div>
  <p>At Marlowby, our mission is to deliver unparalleled aerial access, geotechnical drilling, and service and maintenance solutions, consistently exceeding our clients' expectations. We strive to achieve this by investing in cutting-edge technology, fostering a culture of safety and continuous improvement, and prioritizing environmental sustainability. Through collaboration, integrity, and dedication, we aim to contribute to the success of our clients while maintaining the highes standards of quality and professionalism.</p>
</section>

<section class="divisions">
  <h2 class="section-title">OUR <span>DIVISIONS</span></h2>
  <div class="cards">
    <div class="card aerial" role="img" aria-label="Aerial view of a boom lift over a residential street"><div class="card-shade"></div><h3>AERIAL<br>ACCESS</h3></div>
    <div class="card drilling" role="img" aria-label="Drilling truck parked among trees"><div class="card-shade"></div><h3>GEOTECHNICAL<br>DRILLING</h3></div>
    <div class="card renewable" role="img" aria-label="Worker installing solar panels at sunset"><div class="card-shade"></div><h3>RENEWABLE<br>ENERGY</h3></div>
  </div>
</section>

<section class="services">
  <div class="services-photo" role="img" aria-label="White boom truck parked beside a forest"></div>
  <div class="services-copy">
    <h2 class="section-title">OUR <span>SERVICES</span></h2>
    <p>Delivering safe, reliable aerial access and maintenance services to Oil &amp; Gas, Construction, Utility, &amp; Renewable energy industries.</p>
    <a class="btn" href="#">READ MORE</a>
  </div>
</section>

<footer class="footer">
  <small>Copyright ©2024 CompanyName. All Rights Reserved. Privacy Policy</small>
  <div class="social"><span></span><span></span><span></span><span></span><span></span></div>
</footer>
</body>
</html>
```